PowerPoint Listing Presentation for Real Estate Agency

We need a PowerPoint presentation for a new real estate brokerage team.

[[[[[[submit 1-3 sample slides for review - i will provide feedback and you can make changes if you want to - we will not be deciding on a design prior to the deadline]]]]]

******ATTN: DESIGNERS, if your skills are webdesign then just look at this like a portable website or a brochure. it should be easy enough******

NOTE: we have all the data to put into the slides. You just need to come up with the design and layout. we have a sample design that we like and have provided.

This focus will be for the home listing side of the business (a presentation for home sellers to convince them to use our services). The data and slides will present our team and the benefits, in the best light, to use our services over that of other real estate agent applying for the job. This presentation will proved facts and benefits and describe our special and unique offerings that will show a home seller why we can sell their home for more money in less time and with the least amount of hassle. The main color scheme is Dark Blue and White (we want some additional colors included - based on your creativity. otherwise the presentation will too monotone). We would like to see the use of Statistical Graphs (3-D) - data provided. We have photos of our team and a new logo (the logo could have some minor adjustment to clean it up if necessary) - also uploaded. We have about 80-90% of the information that will be put into the slides and will need to work closely to get the design and data integrated into the presentation (should be easier then it sounds). We should be able to add slides and data 'at will' over time via our master slides built into the presentation. We have a pretty good sample presentation that we like and can be used as a guideline (this is from our affiliated business network and we have full rights to all the information), it is uploaded but doesn't contain all the slide because of size limitations.

NOTE: An additional buyers presentation will be needed after we get the sellers presentation completed, which means additional work.

This should be enough to get you started and we are available if you have any questions to help you with the project. there will be around 60-70 total slides. once concept is completed it will be easy to create the slides.

Target Market(s)

home sellers. people who are moving to a new and better home or relocation for job reasons. typically more established in life

Industry/Entity Type

Real Estate

Requirements
Must have
• all the slides must be congruent. in other words, the exact same layout feel should used across the board. we are working on building our trade dress/image. Also, it must have a soft and inviting overall feel, yet show strength of ability.
Nice to have
• nice to have use of real people images when necessary. 3D graphs would be nice. clean modern look and feel, yet sophisticated and professional.
Should not have
• should not have a lot of time consuming transitions. do not include 3D stick figures or distracting moving gifs

```html
<!DOCTYPE html>
<html lang="en">
<head>
<meta charset="UTF-8">
<title>Project Slide</title>
<link rel="stylesheet" href="https://fonts.googleapis.com/css2?family=Carlito:wght@400;700&family=Open+Sans:wght@400;600&display=swap">
<style>
  :root {
    --navy: #15175c;
    --title-navy: #1b2070;
    --bullet-blue: #3b47c9;
    --body-grey: #545454;
    --bullet-grey: #4a4a4a;
    --footer-text: #a3a8ff;
    --page-ink: #111111;
    --white: #ffffff;
    --swoosh: #ececf0;
    --photo-tone: #bfd2df;
  }
  * { margin: 0; padding: 0; box-sizing: border-box; }
  html, body { width: 1200px; height: 900px; overflow: hidden; background: var(--white); }
  .slide {
    position: relative;
    width: 1200px;
    height: 900px;
    overflow: hidden;
    background: linear-gradient(180deg, #f3f3f6 0%, #ffffff 45%, #ffffff 100%);
    font-family: "Open Sans", Arial, sans-serif;
  }
  .backdrop { position: absolute; inset: 0; }
  .top-band {
    position: absolute; top: 0; left: 0; width: 1200px; height: 42px;
    background: var(--navy);
  }
  .slide-title {
    position: absolute; left: 57px; top: 110px;
    font-family: "Carlito", Calibri, sans-serif;
    font-weight: 400; font-size: 54px; line-height: 1;
    color: var(--title-navy);
  }
  .intro {
    position: absolute; left: 52px; top: 186px; width: 1120px;
    font-size: 23.2px; line-height: 37.5px;
    color: var(--body-grey);
  }
  .points {
    position: absolute; left: 68px; top: 368px;
    list-style: none;
  }
  .points li {
    position: relative; padding-left: 49px;
    font-size: 30px; line-height: 61.5px;
    color: var(--bullet-grey);
  }
  .points li::before {
    content: "\00BB";
    position: absolute; left: 2px; top: -2px;
    font-family: "Carlito", Calibri, sans-serif;
    font-size: 28px; color: var(--bullet-blue);
  }
  .feature-photo {
    position: absolute; left: 785px; top: 414px; width: 348px; height: 222px;
    border: 3px solid var(--white); border-radius: 6px;
    box-shadow: 0 1px 6px rgba(0,0,0,0.35);
    background: var(--photo-tone);
  }
  .footer { position: absolute; left: 0; bottom: 0; width: 1200px; height: 84px; }
  .footer-band { position: absolute; inset: 0; }
  .page-number {
    position: absolute; left: 36px; top: 24px;
    font-family: "Carlito", Calibri, sans-serif;
    font-weight: 700; font-size: 25px; color: var(--page-ink);
  }
  .copyright {
    position: absolute; left: 267px; top: 24px;
    font-size: 23px; color: var(--footer-text);
  }
  .brand-box {
    position: absolute; left: 1042px; top: 786px; width: 104px; height: 104px;
    background: var(--white); border: 4px solid var(--navy);
    display: flex; align-items: center; justify-content: center;
    text-align: center;
  }
  .brand-name {
    font-family: "Open Sans", Arial, sans-serif;
    font-weight: 600; font-size: 16px; line-height: 1.2;
    color: var(--navy);
  }
</style>
</head>
<body>
<main class="slide">
  <svg class="backdrop" width="1200" height="900" viewBox="0 0 1200 900" aria-hidden="true">
    <path d="M300 42 C 600 160, 900 120, 1200 60" fill="none" stroke="var(--swoosh)" stroke-width="40" opacity="0.7"/>
    <path d="M700 42 C 900 200, 1000 400, 1200 520" fill="none" stroke="var(--swoosh)" stroke-width="60" opacity="0.6"/>
    <path d="M0 250 C 400 420, 800 600, 1200 700" fill="none" stroke="#f0f0f4" stroke-width="70" opacity="0.6"/>
  </svg>

  <div class="top-band"></div>

  <h1 class="slide-title">Project Title Here</h1>

  <p class="intro">Lorem ipsum dolor sit ipsum Lorem ipsum dolor sit ipsum Lorem ipsum dolor sit ipsum Lorem<br>ipsum dolor sit ipsum Lorem ipsum dolor sit ipsum Lorem ipsum Lorem ipsum dolor sit ipsum<br>Lorem ipsum dolor sit ipsum Lorem ipsum dolor sit ipsum Lorem ipsum dolor sit ipsum Lorem<br>ipsum dolor sit ipsum Lorem ipsum</p>

  <ul class="points">
    <li>Lorem ipsum dolor sit ipsum</li>
    <li>Lorem ipsum dolor sit ipsum</li>
    <li>Lorem ipsum dolor sit ipsum</li>
    <li>Lorem ipsum dolor sit ipsum</li>
    <li>Lorem ipsum dolor sit ipsum</li>
  </ul>

  <div class="feature-photo" role="img" aria-label="Feature photograph: hands holding a young tree"></div>

  <footer class="footer">
    <svg class="footer-band" width="1200" height="84" viewBox="0 0 1200 84" aria-hidden="true">
      <path d="M147 84 L 205 22 C 215 10, 225 3, 250 2 L 1200 2 L 1200 84 Z" fill="var(--navy)"/>
    </svg>
    <span class="page-number">Page : 02</span>
    <span class="copyright">Copyright text here</span>
  </footer>

  <div class="brand-box">
    <span class="brand-name">Harlow &amp;<br>Finch</span>
  </div>
</main>
</body>
</html>
```